Nanny Share Ecommerce Website for Finding Childcare and Parents who need Childcare BrightPramHub.net

Our company needs an ecommerce website (BrightPramHub.net) for a US subscription based service strictly for nanny sharing that connects families and caregivers. The website would allow families to connect with one another as well as to search for nannies. The service would be searchable for other families by location (by radius or zip code), children demographic (age range/gender/special needs), days of week or times, after school care, school closure days (holidays), etc. The service would also be searchable for nannies based on gender, provider age range, years experience, language, hourly rate, transportation available, certification (CPR first aid), education etc. The search fields would be searchable and sortable and allow to connect with the provider (after paying subscription fee). The service would be similar to tendlyfolk.net in that it would allow for families and caregivers to post photos as well as a short bio of the themselves. There would also be a feedback/star rating mechanism to rate caregivers who have performed work for families (viewable to public). The service would be free for nannies to post their bios and only a subscription based service for families to connect with other families or with caregivers (able to view bio but need service to connect). There will be a short bio on the benefits of nanny sharing (reduced cost, increased flexibility for parents, reduced illness, increased socialization with other children vs. sole nanny), as well as Q&A section with best practices.

Target Market(s)

Families, Nannies

Industry/Entity Type

Childcare

Logo Text

Bright Pram Hub

Coding

Coded - Design and coding required

Number of Pages Required

5+ page

Requirements
Must have
• Searchable (need to be able to search for families as well as nannies), responsive, functional, easy to use, add value to families and nannies. Needs to be able to collect payment for subscription.
Nice to have
• Optimized for mobile, SEO optimized

```html
<!DOCTYPE html>
<html lang="en">
<head>
<meta charset="utf-8">
<title>Bright Pram Hub — Nanny Sharing</title>
<link href="https://fonts.googleapis.com/css2?family=Lato:wght@400;700;900&family=Open+Sans:wght@400;600;700&display=swap" rel="stylesheet">
<style>
:root{
  --blue:#1f6fb6;
  --blue-dark:#175a96;
  --orange:#f5862a;
  --ink:#222;
  --muted:#777;
  --line:#e3e3e3;
  --white:#fff;
}
*{box-sizing:border-box;margin:0;padding:0}
html,body{width:1200px;height:4045px;overflow:hidden}
body{position:relative;font-family:"Open Sans",sans-serif;color:var(--ink);background:var(--white)}
.abs{position:absolute}
h2.section-title{position:absolute;left:0;width:1200px;text-align:center;font-family:"Lato",sans-serif;font-weight:900;font-size:30px;letter-spacing:.5px;color:var(--ink)}
.small{font-size:12px;line-height:20px;color:var(--muted)}
.btn{position:absolute;display:flex;align-items:center;justify-content:center;border-radius:22px;font-family:"Lato",sans-serif;font-weight:700;font-size:13px;color:var(--white);letter-spacing:.5px}
.btn-outline{position:absolute;display:flex;align-items:center;justify-content:center;border:2px solid var(--line);border-radius:20px;font-family:"Lato",sans-serif;font-weight:700;font-size:12px;color:var(--orange);background:var(--white)}

/* header */
.site-header{position:absolute;left:0;top:0;width:1200px;height:113px;background:var(--white);box-shadow:0 2px 6px rgba(0,0,0,.08);z-index:2}
.brand{left:135px;top:30px;display:flex;align-items:center;gap:10px;font-family:"Lato",sans-serif;font-weight:900;font-size:17px;color:var(--orange)}
.brand-dot{width:28px;height:28px;border-radius:50%;background:var(--blue)}
.topbar{right:110px;top:28px;display:flex;align-items:center;gap:22px;font-size:13px;color:#555}
.topbar .sep{width:1px;height:16px;background:#ccc}
.login{background:var(--orange);color:var(--white);border-radius:14px;padding:4px 14px;font-weight:700;font-size:12px}
.nav{right:110px;top:76px;display:flex;gap:38px;font-family:"Lato",sans-serif;font-weight:700;font-size:13px;color:#333;letter-spacing:.3px}
.nav .active{color:var(--orange);border-bottom:2px solid var(--orange);padding-bottom:6px}

/* hero */
.hero{left:0;top:113px;width:1200px;height:561px;
  background:
    radial-gradient(ellipse 260px 220px at 680px 420px,rgba(214,52,58,.85),rgba(214,52,58,0) 75%),
    radial-gradient(ellipse 300px 260px at 420px 200px,rgba(228,190,120,.9),rgba(228,190,120,0) 75%),
    radial-gradient(ellipse 200px 170px at 640px 220px,rgba(240,200,170,.9),rgba(240,200,170,0) 75%),
    radial-gradient(ellipse 260px 300px at 80px 300px,rgba(130,150,110,.6),rgba(130,150,110,0) 75%),
    linear-gradient(100deg,#d8c0ae 0%,#efe3da 40%,#ece8e6 70%,#d8dde4 100%)}
.hero-title{left:0;top:395px;width:1200px;text-align:center;font-family:"Lato",sans-serif;font-weight:900;font-size:54px;color:var(--white);text-shadow:0 2px 8px rgba(0,0,0,.35)}
.slider-arrow{width:34px;height:34px;border-radius:50%;background:rgba(0,0,0,.35);display:flex;align-items:center;justify-content:center}

.option-card{left:130px;top:526px;width:862px;height:297px;background:var(--white);box-shadow:0 4px 18px rgba(0,0,0,.12)}
.option-card h3{position:absolute;left:0;top:46px;width:862px;text-align:center;font-family:"Lato",sans-serif;font-weight:900;font-size:20px}
.option-col{position:absolute;top:122px;width:330px;text-align:center}
.option-col h4{font-family:"Lato",sans-serif;font-weight:700;font-size:15px;margin-bottom:12px}

/* services */
.service-card{position:absolute;top:1038px;width:224px;height:351px;background:var(--white);box-shadow:0 2px 10px rgba(0,0,0,.1)}
.service-photo{position:absolute;left:8px;top:8px;width:208px;height:168px}
.service-icon{position:absolute;left:74px;top:-22px;width:76px;height:76px;border-radius:50%;background:var(--blue);border:4px solid var(--white);display:flex;align-items:center;justify-content:center}
.service-card h3{position:absolute;left:0;top:203px;width:224px;text-align:center;font-family:"Lato",sans-serif;font-weight:700;font-size:20px}
.service-card p{position:absolute;left:20px;top:240px;width:184px;text-align:center}

/* benefits */
.benefits{left:0;top:1478px;width:1200px;height:499px;
  background:
    linear-gradient(180deg,rgba(31,111,182,.86),rgba(23,90,150,.92)),
    radial-gradient(ellipse 300px 200px at 300px 300px,#5b8a4a,transparent),
    radial-gradient(ellipse 300px 200px at 900px 250px,#4f7d58,transparent),
    linear-gradient(90deg,#4a7f5a,#3b6fa0)}
.benefit{position:absolute;top:1664px;width:260px;text-align:center;color:var(--white)}
.benefit-ring{margin:0 auto;width:124px;height:124px;border-radius:50%;border:5px solid rgba(255,255,255,.8);display:flex;align-items:center;justify-content:center}
.benefit-core{width:100px;height:100px;border-radius:50%;background:var(--white);display:flex;align-items:center;justify-content:center}
.benefit h3{margin-top:26px;font-family:"Lato",sans-serif;font-weight:700;font-size:21px}
.benefit p{margin-top:8px;font-size:12px;line-height:20px;color:#dbe8f5}

/* about */
.about-video{left:102px;top:2071px;width:464px;height:302px;
  background:
    radial-gradient(ellipse 90px 120px at 240px 190px,rgba(200,60,60,.8),transparent 75%),
    radial-gradient(ellipse 120px 90px at 140px 230px,rgba(90,90,100,.8),transparent 75%),
    linear-gradient(180deg,#4d7a3a 0%,#7fa65a 45%,#a9b979 75%,#c8b48a 100%);
  border:6px solid var(--white);box-shadow:0 2px 10px rgba(0,0,0,.15)}
.about h2{position:absolute;left:626px;top:2068px;font-family:"Lato",sans-serif;font-weight:900;font-size:28px}
.about p{position:absolute;left:626px;width:474px}

/* testimonials */
.testimonials{left:0;top:2468px;width:1200px;height:399px;
  background:
    radial-gradient(ellipse 260px 300px at 420px 200px,rgba(200,140,90,.9),transparent 75%),
    radial-gradient(ellipse 260px 260px at 920px 320px,rgba(190,40,45,.9),transparent 75%),
    linear-gradient(90deg,#7a4a30,#b47a52 45%,#6e3d34 75%,#9a3a3a)}
.testimonials-shade{left:0;top:2468px;width:1200px;height:399px;background:rgba(0,0,0,.35)}
.review{position:absolute;top:2630px;width:320px;color:var(--white)}
.avatar{position:absolute;left:0;top:0;width:64px;height:64px;border-radius:50%;background:radial-gradient(circle at 50% 40%,#e2c3a8,#8a5e44);border:3px solid var(--white)}
.review p{position:absolute;left:80px;top:0;width:240px;font-size:12px;line-height:20px;font-style:italic;color:#eee}
.stars{position:absolute;left:80px;top:82px;color:#f7c31a;font-size:16px;letter-spacing:3px}
.review .name{position:absolute;left:80px;top:112px;font-weight:700;font-size:13px}
.review .role{position:absolute;left:80px;top:136px;font-size:12px;color:#ddd}

/* faq */
.faq-open-head{position:absolute;width:477px;height:40px;background:var(--orange);color:var(--white);font-size:14px;font-weight:600;display:flex;align-items:center;padding-left:16px}
.faq-toggle{position:absolute;right:0;top:0;width:40px;height:100%;background:var(--blue);color:var(--white);display:flex;align-items:center;justify-content:center;font-weight:700;font-size:18px}
.faq-body{position:absolute;width:477px;height:108px;border:1px solid var(--line);border-top:none;padding:16px 26px}
.faq-item{position:absolute;width:477px;height:44px;border:1px solid var(--line);font-size:14px;color:#333;display:flex;align-items:center;padding-left:16px}

/* contact */
.contact-bg{left:0;top:3452px;width:1200px;height:526px;
  background:
    linear-gradient(180deg,rgba(33,118,192,.96) 0%,rgba(33,118,192,.9) 60%,rgba(26,102,171,.85) 100%),
    linear-gradient(0deg,#5e8fc0 0%,#5e8fc0 22%,transparent 22%)}
.contact-title{position:absolute;left:0;top:3518px;width:1200px;text-align:center;font-family:"Lato",sans-serif;font-weight:900;font-size:30px;color:var(--white)}
.contact-sub{position:absolute;left:0;top:3578px;width:1200px;text-align:center;font-size:13px;color:#dbe8f5}
.field{position:absolute;height:43px;border:1px solid rgba(255,255,255,.6);font-size:12px;color:#e4eef8;padding:13px 16px}
.info{position:absolute;top:3882px;display:flex;align-items:center;gap:16px;color:var(--white);font-size:13px;line-height:22px}
.info-icon{width:48px;height:48px;border-radius:50%;background:var(--white);display:flex;align-items:center;justify-content:center}
.footer{left:0;top:3978px;width:1200px;height:67px;background:var(--orange);color:var(--white);font-size:13px}
.social{width:30px;height:30px;border-radius:50%;background:var(--white)}
</style>
</head>
<body>

<header class="site-header">
  <div class="abs brand"><span class="brand-dot"></span>Bright Pram Hub</div>
  <div class="abs topbar">
    <span>&#9742; (+1) 123 456 7890</span><span class="sep"></span>
    <span>&#9993; info@brightpramhub.net</span>
    <span class="login">&#128274; LOGIN</span>
  </div>
  <nav class="abs nav">
    <span class="active">HOME</span><span>ABOUT</span><span>SERVICES &#9662;</span><span>HOW IT WORKS</span><span>BLOG</span><span>CONTACT</span><span>&#9906;</span>
  </nav>
</header>

<section>
  <div class="abs hero" role="img" aria-label="Photo of a smiling mother playing with her toddler daughter at home"></div>
  <div class="abs slider-arrow" style="left:28px;top:378px"><svg width="12" height="12"><path d="M8 1 3 6l5 5" stroke="#fff" stroke-width="2" fill="none"/></svg></div>
  <div class="abs slider-arrow" style="left:1138px;top:378px"><svg width="12" height="12"><path d="M4 1l5 5-5 5" stroke="#fff" stroke-width="2" fill="none"/></svg></div>
  <h1 class="abs hero-title">BRIGHT PRAM HUB</h1>

  <div class="abs option-card">
    <h3>LET'S GET STARTED. CHOOSE AN OPTION.</h3>
    <div class="option-col" style="left:80px">
      <h4>I NEED A CAREGIVER</h4>
      <p class="small">At vero eos et accusamus et iusto dignissimos.</p>
    </div>
    <div class="option-col" style="left:452px">
      <h4>SEARCH FOR NANNIES</h4>
      <p class="small">At vero eos et accusamus et iusto dignissimos.</p>
    </div>
    <div class="btn" style="left:178px;top:208px;width:130px;height:40px;background:var(--orange)">FIND CARE</div>
    <div class="btn" style="left:552px;top:208px;width:130px;height:40px;background:var(--blue)">FIND NANNY</div>
  </div>
</section>

<section>
  <h2 class="section-title" style="top:912px">OUR SERVICES</h2>

  <article class="service-card" style="left:100px">
    <div class="service-photo" role="img" aria-label="Photo of children playing with toy blocks" style="background:radial-gradient(ellipse 80px 60px at 60% 65%,#e0513f,transparent 75%),radial-gradient(ellipse 70px 60px at 30% 40%,#f6d9b8,transparent 75%),linear-gradient(135deg,#f2c46a,#e58a5a)"></div>
    <div class="service-icon"><svg width="34" height="34" viewBox="0 0 34 34"><circle cx="17" cy="9" r="5" fill="#fff"/><path d="M7 30c0-8 4-13 10-13s10 5 10 13z" fill="#fff"/></svg></div>
    <h3>Child Care</h3>
    <p class="small">At vero eos et accusamus et iusto odio dignissimos ducimus</p>
    <div class="btn-outline" style="left:44px;top:315px;width:136px;height:38px">READ MORE &#10148;</div>
  </article>

  <article class="service-card" style="left:359px">
    <div class="service-photo" role="img" aria-label="Photo of an older woman laughing with a caregiver" style="background:radial-gradient(ellipse 70px 80px at 30% 50%,#e8c9b2,transparent 75%),radial-gradient(ellipse 70px 90px at 75% 60%,#c23a3a,transparent 75%),linear-gradient(135deg,#c9a48a,#7c6a5e)"></div>
    <div class="service-icon"><svg width="34" height="34" viewBox="0 0 34 34"><circle cx="17" cy="7" r="4" fill="#fff"/><path d="M12 31l2-13h6l2 13zM22 18l5 13" stroke="#fff" stroke-width="2.5" fill="#fff"/></svg></div>
    <h3>Senior Care</h3>
    <p class="small">At vero eos et accusamus et iusto odio dignissimos ducimus</p>
    <div class="btn-outline" style="left:44px;top:315px;width:136px;height:38px">READ MORE &#10148;</div>
  </article>

  <article class="service-card" style="left:618px">
    <div class="service-photo" role="img" aria-label="Photo of a pet sitter with a dog" style="background:radial-gradient(ellipse 90px 60px at 40% 75%,#2f5ea8,transparent 75%),radial-gradient(ellipse 80px 70px at 70% 40%,#b88a5c,transparent 75%),linear-gradient(135deg,#8d6a48,#3c4b5e)"></div>
    <div class="service-icon"><svg width="34" height="34" viewBox="0 0 34 34"><circle cx="9" cy="12" r="3" fill="#fff"/><circle cx="15" cy="7" r="3" fill="#fff"/><circle cx="21" cy="7" r="3" fill="#fff"/><circle cx="27" cy="12" r="3" fill="#fff"/><ellipse cx="18" cy="23" rx="7" ry="6" fill="#fff"/></svg></div>
    <h3>Pet Care</h3>
    <p class="small">At vero eos et accusamus et iusto odio dignissimos ducimus</p>
    <div class="btn-outline" style="left:44px;top:315px;width:136px;height:38px">READ MORE &#10148;</div>
  </article>

  <article class="service-card" style="left:876px">
    <div class="service-photo" role="img" aria-label="Photo of a home carer helping an elderly man" style="background:radial-gradient(ellipse 80px 90px at 75% 55%,#2c3f66,transparent 75%),radial-gradient(ellipse 70px 70px at 30% 50%,#e6e1dc,transparent 75%),linear-gradient(135deg,#d9d4cf,#5c6e84)"></div>
    <div class="service-icon"><svg width="34" height="34" viewBox="0 0 34 34"><path d="M4 17 17 5l13 12h-4v12H8V17z" fill="#fff"/></svg></div>
    <h3>Home Care</h3>
    <p class="small">At vero eos et accusamus et iusto odio dignissimos ducimus</p>
    <div class="btn-outline" style="left:44px;top:315px;width:136px;height:38px">READ MORE &#10148;</div>
  </article>
</section>

<section>
  <div class="abs benefits" role="img" aria-label="Blue-tinted photo of a family walking in a park"></div>
  <h2 class="section-title" style="top:1562px;color:var(--white)">OUR BENEFITS</h2>

  <div class="benefit" style="left:80px">
    <div class="benefit-ring"><div class="benefit-core"><svg width="50" height="50" viewBox="0 0 50 50"><text x="25" y="38" text-anchor="middle" font-family="Lato,sans-serif" font-weight="900" font-size="40" fill="#f5862a">$</text></svg></div></div>
    <h3>Reduced Cost</h3>
    <p>At vero eos et accusamus et iusto odio dignissimos ducimus blanditiis</p>
  </div>
  <div class="benefit" style="left:340px">
    <div class="benefit-ring"><div class="benefit-core"><svg width="50" height="50" viewBox="0 0 50 50"><path d="M6 42h40M6 42V8" stroke="#f5862a" stroke-width="3" fill="none"/><path d="M10 36l10-12 8 7 14-17" stroke="#f5862a" stroke-width="3.5" fill="none"/><path d="M36 13h7v7" stroke="#f5862a" stroke-width="3.5" fill="none"/></svg></div></div>
    <h3>Increased Flexibility</h3>
    <p>At vero eos et accusamus et iusto odio dignissimos ducimus blanditiis</p>
  </div>
  <div class="benefit" style="left:600px">
    <div class="benefit-ring"><div class="benefit-core"><svg width="52" height="52" viewBox="0 0 52 52"><path d="M26 46 8 28a10 10 0 0 1 18-14 10 10 0 0 1 18 14z" fill="#f5862a"/><path d="M8 26h10l4-8 6 14 4-6h12" stroke="#fff" stroke-width="3" fill="none"/></svg></div></div>
    <h3>Reduced Illness</h3>
    <p>At vero eos et accusamus et iusto odio dignissimos ducimus blanditiis</p>
  </div>
  <div class="benefit" style="left:860px">
    <div class="benefit-ring"><div class="benefit-core"><svg width="52" height="52" viewBox="0 0 52 52"><circle cx="26" cy="12" r="6" fill="#f5862a"/><circle cx="12" cy="34" r="6" fill="#f5862a"/><circle cx="40" cy="34" r="6" fill="#f5862a"/><path d="M26 18v8M26 26l-10 4M26 26l10 4" stroke="#f5862a" stroke-width="3"/><path d="M4 48c0-5 4-8 8-8s8 3 8 8M32 48c0-5 4-8 8-8s8 3 8 8" stroke="#f5862a" stroke-width="3" fill="none"/></svg></div></div>
    <h3>Increased Socialization</h3>
    <p>At vero eos et accusamus et iusto odio dignissimos ducimus blanditiis</p>
  </div>
</section>

<section class="about">
  <div class="abs about-video" role="img" aria-label="Video still of a caregiver pushing an elderly man in a wheelchair through a park"></div>
  <svg class="abs" style="left:302px;top:2190px" width="64" height="64" viewBox="0 0 64 64"><circle cx="32" cy="32" r="30" fill="#e0262b"/><path d="M26 20v24l18-12z" fill="#fff"/></svg>
  <h2>ABOUT BRIGHT PRAM HUB</h2>
  <p class="small" style="top:2132px">At vero eos et accusamus et iusto odio dignissimos ducimus blanditiis praesentium voluptatum deleniti atque.</p>
  <p class="small" style="top:2206px">Occaecati cupiditate non provident, similique sunt in culpa qui officia deserunt mollitia animi, id est laborum et dolorum fuga. Et harum quidem rerum facilis est et expedita distinctio. Nam libero tempore, cum soluta nobis est eligendi optio cumque nihil impedit quo minus.</p>
  <div class="btn-outline" style="left:626px;top:2332px;width:146px;height:40px">READ MORE &#10148;</div>
</section>

<section>
  <div class="abs testimonials" role="img" aria-label="Photo of a mother and daughter in warm indoor light"></div>
  <div class="abs testimonials-shade"></div>
  <h2 class="section-title" style="top:2544px;color:var(--white)">WHAT OUR CLIENTS SAY</h2>
  <div class="abs slider-arrow" style="left:12px;top:2690px"><svg width="12" height="12"><path d="M8 1 3 6l5 5" stroke="#fff" stroke-width="2" fill="none"/></svg></div>
  <div class="abs slider-arrow" style="left:1154px;top:2690px"><svg width="12" height="12"><path d="M4 1l5 5-5 5" stroke="#fff" stroke-width="2" fill="none"/></svg></div>

  <div class="review" style="left:100px">
    <div class="avatar" role="img" aria-label="Client portrait photo"></div>
    <p>At vero eos et accusamus et iustodio dignissimos ducimus qui blanditpraesent ium voluptatum deleniti atque.</p>
    <div class="stars">&#9733;&#9733;&#9733;&#9733;&#9733;</div>
    <div class="name">MARA LIND</div>
    <div class="role">Creative Manager, USA</div>
  </div>
  <div class="review" style="left:450px">
    <div class="avatar" role="img" aria-label="Client portrait photo"></div>
    <p>At vero eos et accusamus et iustodio dignissimos ducimus qui blanditpraesent ium voluptatum deleniti atque.</p>
    <div class="stars">&#9733;&#9733;&#9733;&#9733;&#9733;</div>
    <div class="name">TED VOLLAN</div>
    <div class="role">Creative Manager, USA</div>
  </div>
  <div class="review" style="left:801px">
    <div class="avatar" role="img" aria-label="Client portrait photo"></div>
    <p>At vero eos et accusamus et iustodio dignissimos ducimus qui blanditpraesent ium voluptatum deleniti atque.</p>
    <div class="stars">&#9733;&#9733;&#9733;&#9733;&#9733;</div>
    <div class="name">IVO BRANDT</div>
    <div class="role">Creative Manager, USA</div>
  </div>
</section>

<section>
  <h2 class="section-title" style="top:2956px">FREQUENTLY ASKED QUESTIONS</h2>

  <div class="faq-open-head" style="left:100px;top:3048px">What is Lorem Ipsum?<span class="faq-toggle">&minus;</span></div>
  <div class="faq-body small" style="left:100px;top:3088px">Nemo enim ipsam voluptatem quia voluptas sit aspernatur aut odit aut fugit, sed quia consequuntur magni dolores eos qui ratione voluptatem sequi nesciunt. Neque porro quisquam est, qui dolorem.</div>
  <div class="faq-item" style="left:100px;top:3214px">What is Itaque Earum?<span class="faq-toggle">+</span></div>
  <div class="faq-item" style="left:100px;top:3265px">What is Weakness Of Will?<span class="faq-toggle">+</span></div>
  <div class="faq-item" style="left:100px;top:3316px">What is Perfectly Simple?<span class="faq-toggle">+</span></div>

  <div class="faq-open-head" style="left:623px;top:3048px">Nothing Prevents Our Being Able To do?<span class="faq-toggle">&minus;</span></div>
  <div class="faq-body small" style="left:623px;top:3088px">Nemo enim ipsam voluptatem quia voluptas sit aspernatur aut odit aut fugit, sed quia consequuntur magni dolores eos qui ratione voluptatem sequi nesciunt. Neque porro quisquam est, qui dolorem.</div>
  <div class="faq-item" style="left:623px;top:3214px">When Our Power Of Choice?<span class="faq-toggle">+</span></div>
  <div class="faq-item" style="left:623px;top:3265px">Rejects Pleasures To Secure?<span class="faq-toggle">+</span></div>
  <div class="faq-item" style="left:623px;top:3316px">Perfectly Simple &amp; Easy To Distinguish?<span class="faq-toggle">+</span></div>
</section>

<section class="quick-contact">
  <div class="abs contact-bg" role="img" aria-label="Faint city skyline over a blue background"></div>
  <h2 class="contact-title">QUICK CONTACT</h2>
  <p class="contact-sub">At vero eos et accusamus et iusto odio dignissimos ducimus qui blanditiis praesentium voluptatum</p>
  <div class="field" style="left:197px;top:3622px;width:261px">Enter Name</div>
  <div class="field" style="left:469px;top:3622px;width:260px">Email Address</div>
  <div class="field" style="left:739px;top:3622px;width:261px">Phone</div>
  <div class="field" style="left:197px;top:3681px;width:803px;height:76px">Message</div>
  <div class="btn" style="left:518px;top:3786px;width:162px;height:44px;background:var(--orange)">SUBMIT NOW</div>

  <div class="info" style="left:112px">
    <div class="info-icon"><svg width="22" height="22" viewBox="0 0 22 22"><path d="M11 21s-7-7-7-12a7 7 0 0 1 14 0c0 5-7 12-7 12z" fill="#f5862a"/><circle cx="11" cy="9" r="2.5" fill="#fff"/></svg></div>
    <div>1234 Y Sample Street, Old City,<br>New State, ABC.</div>
  </div>
  <div class="info" style="left:490px">
    <div class="info-icon"><svg width="22" height="22" viewBox="0 0 22 22"><path d="M5 2l4 4-2 3c1 2 3 4 5 5l3-2 4 4-3 3C9 19 3 13 2 5z" fill="#f5862a"/></svg></div>
    <div>Phone: (+1) 123 456 7890<br>Fax: (+1) 888 888 8888</div>
  </div>
  <div class="info" style="left:764px">
    <div class="info-icon"><svg width="22" height="22" viewBox="0 0 22 22"><circle cx="11" cy="11" r="9" stroke="#f5862a" stroke-width="2.5" fill="none"/><path d="M11 6v5l3 3" stroke="#f5862a" stroke-width="2.5" fill="none"/></svg></div>
    <div>Monday - Saturday &nbsp;: &nbsp;8:00am - 10:00pm<br>Sunday &nbsp;: &nbsp;10:00am - 4:00pm</div>
  </div>
</section>

<footer class="abs footer">
  <div class="abs" style="left:100px;top:24px">&copy; Copyright 2018 Bright Pram Hub. All Rights Reserved.</div>
  <div class="abs" style="left:960px;top:18px;display:flex;gap:10px" aria-label="Social links">
    <span class="social"></span><span class="social"></span><span class="social"></span><span class="social"></span>
  </div>
</footer>

</body>
</html>
```